Kraft Eco-friendly pouch back imprint

Updating the design imprint on the back of our eco-friendly kraft stand up pouches. The current package back is a story letter but we want to change it to be more visually eye catching and make better use of buzzwords and graphics. I've uploaded a PDF with the current graphic so that key buzz words and thoughts could be pulled and highlighted.

The printing will be done in black and white, so don't spend time with colors. The imprint area is approximately 7" high x 5" wide.

I definitely want our logo at the top of the package, and I'm attaching two options.

Our mission is to be the Healthiest Pet Bakery in the U.S. That needs to be another point of emphasis.

Other potential buzzwords or bullets include:
Artisan Recipes
Simple Ingredients
No corn, wheat, soy, GMOs, or preservatives
Handcrafted
Locally sourced (Pacific NW)
Eco-conscious company
Updates

The system only allowed 24 hours. That is a ridiculously short time window.

Target Market(s)

Pet parents seeking natural, healthy products

Industry/Entity Type

independent pet channel

Colors

Designer to choose only greyscale colors for use in the design.

Requirements
Must have
• Logo, Mission, buzz words, graphics

```html
<!DOCTYPE html>
<html lang="en">
<head>
<meta charset="utf-8">
<title>Biscuit Harbor Bakery – Pouch Back Imprint</title>
<link href="https://fonts.googleapis.com/css2?family=Montserrat:wght@400;500;700;800&family=Pathway+Gothic+One&family=Barlow+Semi+Condensed:wght@400&display=swap" rel="stylesheet">
<style>
  :root {
    --ink: #1b1b1b;
    --paper: #ffffff;
    --stage: #ffffff;
    --panel-grey: #d9d9d9;
    --tile-grey: #d4d4d4;
    --art-grey: #8c8c8c;
    --map-grey: #a6a6a6;
    --frame: #555555;
  }
  * { box-sizing: border-box; margin: 0; padding: 0; }
  html, body { width: 1200px; height: 998px; overflow: hidden; background: var(--stage); }
  body { position: relative; font-family: "Montserrat", sans-serif; color: var(--ink); }

  .imprint {
    position: absolute; left: 256px; top: 19px; width: 687px; height: 960px;
    background: var(--paper); border: 1px solid var(--frame);
  }
  .imprint > * { position: absolute; }

  /* brand */
  .brand-mark { left: 98px; top: 62px; width: 100px; height: 100px; border-radius: 50%; background: var(--art-grey); }
  .brand-name {
    left: 222px; top: 92px; width: 360px;
    font-weight: 700; font-size: 38px; line-height: 1.1; color: var(--ink);
  }

  /* year + mission */
  .year-banner { left: 69px; top: 274px; width: 158px; height: 56px; }
  .year-banner svg { position: absolute; left: 0; top: 0; }
  .year-banner span {
    position: absolute; left: 24px; top: 6px; font-weight: 800; font-size: 36px; color: var(--paper);
  }
  .rocket-art { left: 238px; top: 234px; width: 72px; height: 76px; background: linear-gradient(135deg, #7a7a7a, #3a3a3a); }
  .mission { left: 73px; top: 336px; font-size: 17px; line-height: 1.22; }
  .mission strong { font-weight: 700; display: block; }

  .story-card {
    left: 283px; top: 272px; width: 332px; height: 148px; padding: 12px 16px;
    background: var(--panel-grey); border-radius: 12px; transform: rotate(3deg);
    font-size: 16px; line-height: 1.3;
  }

  /* free-from tiles */
  .free-from { left: 69px; top: 410px; width: 200px; display: grid; grid-template-columns: 93px 93px; gap: 8px; }
  .free-tile {
    height: 70px; background: var(--tile-grey); border-radius: 6px; position: relative;
    transform: rotate(-3deg);
  }
  .free-tile .tile-icon { position: absolute; left: 8px; top: 14px; width: 30px; height: 42px; background: var(--art-grey); border-radius: 40%; }
  .free-tile .tile-label {
    position: absolute; left: 42px; top: 6px; font-family: "Pathway Gothic One", sans-serif;
    font-size: 26px; line-height: 0.95; text-align: center; color: var(--ink);
  }
  .free-tile .tile-label small { display: block; font-size: 20px; }

  /* headlines */
  .headline-simple { left: 290px; top: 442px; font-weight: 800; font-size: 26px; letter-spacing: 0.3px; }
  .ribbon-artisan { left: 283px; top: 470px; width: 334px; height: 82px; }
  .ribbon-artisan svg { position: absolute; left: 0; top: 0; }
  .ribbon-artisan span {
    position: absolute; left: 16px; top: 20px; font-weight: 800; font-size: 31px; color: var(--paper);
    transform: rotate(3deg); white-space: nowrap;
  }

  /* local sourcing */
  .local-card {
    left: 69px; top: 586px; width: 550px; height: 72px; padding: 6px 14px;
    background: var(--panel-grey); border-radius: 8px;
    font-family: "Barlow Semi Condensed", sans-serif; font-size: 16.5px; line-height: 1.24;
  }
  .local-card p { width: 392px; }
  .region-map { left: 482px; top: 556px; width: 54px; height: 124px; background: var(--map-grey); border-radius: 4px; }
  .region-label { left: 542px; top: 554px; font-family: "Pathway Gothic One", sans-serif; font-size: 26px; line-height: 0.95; text-align: right; width: 58px; }

  /* handcrafted */
  .ribbon-handcrafted { left: 71px; top: 684px; width: 322px; height: 140px; }
  .ribbon-handcrafted svg { position: absolute; left: 0; top: 0; }
  .ribbon-handcrafted .hand-word {
    position: absolute; left: 16px; top: 16px; font-weight: 800; font-size: 33px; color: var(--paper); transform: rotate(-2deg); white-space: nowrap;
  }
  .ribbon-handcrafted .eco-word {
    position: absolute; left: 17px; top: 80px; font-weight: 800; font-size: 25px; line-height: 0.9; color: var(--ink);
  }
  .heart-icon { left: 380px; top: 668px; width: 26px; height: 24px; }

  .sign-off { left: 73px; top: 830px; font-size: 16.5px; line-height: 1.38; }
  .sign-off .site { font-weight: 700; }

  .eco-card {
    left: 389px; top: 693px; width: 232px; height: 212px; padding: 10px 13px;
    background: var(--panel-grey); border-radius: 14px; transform: rotate(3deg);
    font-size: 15px; line-height: 1.3; text-align: justify;
  }
  .eco-card .spaced { letter-spacing: 3.5px; }
</style>
</head>
<body>
  <main class="imprint">
    <div class="brand-mark" aria-hidden="true"></div>
    <div class="brand-name">Biscuit Harbor<br>Bakery</div>

    <div class="year-banner">
      <svg width="158" height="56" viewBox="0 0 158 56" aria-hidden="true">
        <path d="M0 10 L158 0 L154 46 L0 56 Z" fill="#1b1b1b"/>
      </svg>
      <span>2017</span>
    </div>
    <div class="rocket-art" role="img" aria-label="Rocket illustration"></div>

    <p class="mission"><strong>Our mission</strong>is to be the healthiest<br>pet bakery in the U.S.A.</p>

    <p class="story-card">Biscuit Harbor Bakery was acquired by a couple in Pine Hollow, WA in 2017 (originally founded in 2004) and who also own and operate two independent pet health food stores.</p>

    <div class="free-from">
      <div class="free-tile"><div class="tile-icon" role="img" aria-label="Wheat icon"></div><div class="tile-label">NO<small>WHEAT</small></div></div>
      <div class="free-tile"><div class="tile-icon" role="img" aria-label="Corn icon"></div><div class="tile-label">NO<small>CORN</small></div></div>
      <div class="free-tile"><div class="tile-icon" role="img" aria-label="Soybean icon"></div><div class="tile-label">NO<small>SOY</small></div></div>
      <div class="free-tile"><div class="tile-icon" role="img" aria-label="Lab flask icon"></div><div class="tile-label">NO<small>GMOs</small></div></div>
    </div>

    <h2 class="headline-simple">SIMPLE INGREDIENTS</h2>
    <div class="ribbon-artisan">
      <svg width="334" height="82" viewBox="0 0 334 82" aria-hidden="true">
        <path d="M8 8 Q170 -4 334 2 L326 64 Q170 56 0 82 Z" fill="#1b1b1b"/>
      </svg>
      <span>ARTISAN RECIPES</span>
    </div>

    <div class="local-card"><p>Our treats are hand crafted using only the highest quality human grade ingredients, which are sourced as locally as possible in the Pacific Northwest.</p></div>
    <div class="region-map" role="img" aria-label="Map of the Pacific Northwest region"></div>
    <div class="region-label">PACIFIC<br>NW</div>

    <div class="ribbon-handcrafted">
      <svg width="322" height="140" viewBox="0 0 322 140" aria-hidden="true">
        <path d="M0 0 Q160 14 312 8 L322 58 Q160 50 6 72 Z" fill="#1b1b1b"/>
        <path d="M240 100 L300 86 L322 58 L318 112 L280 130 L300 104 Z" fill="#1b1b1b"/>
      </svg>
      <span class="hand-word">HANDCRAFTED</span>
      <span class="eco-word">ECO-CONSCIOUS<br>COMPANY</span>
    </div>
    <svg class="heart-icon" viewBox="0 0 26 24" aria-hidden="true">
      <path d="M13 23 L2 11 A6 6 0 0 1 13 4 A6 6 0 0 1 24 11 Z" fill="#1b1b1b"/>
    </svg>

    <p class="sign-off">Your friends @ Biscuit Harbor Bakery<br><span class="site">www.biscuitharborbakery.com</span><br>Cedar Cove, WA &nbsp;&nbsp;866-555-0142</p>

    <p class="eco-card"><span class="spaced">We focus on the</span> environment and this package reflects our commitment to reducing our carbon pawprint. We hope that your furry friend enjoys our hand-crafted treats as much as we enjoy making them.</p>
  </main>
</body>
</html>
```